Environmental Consultancey needs Web Design

A consultancey firm based in Papua New Guinea specialising servicing a client market primarily in Melanesia, the wider Pacific Region and South East Asia. The firm provides services to community development and resource extraction activites that incorporate sustainable livelihoods for local customary land owners with environmentally responsibile practices and a focus on maintaining biodiversity and ecosystem services. We aim to encompass Culture, Custom and Science in our approach. Our website preferentially will convey a relaxed Pacific Island feel in its colours and design rather than a sterile corporate feel. See attached logo that will need to be visible on page or which may provide basis for ideas for the page.

Target Market(s)

Our target market is primarily the oil, gas and mining industry, secondarily international donor and aid programs followed by government projects and not for profit programs. Services include:
1. Biodiversity and Conservation - Fauna and Flora survey, assessment, management, monitoring & research, protected areas & endangered & threatend species.
2. Social & Community - impact, stakeholder engagement, census and survey, land and community affairs, capacity building empowerment.
3. Environmental Management - sustainable use, enterprise development & management, biodiversity offsets.

Industry/Entity Type

Community

Requirements
Must have
• Multiple pages, Logo somewhere on home page. Space for a couple of photos that as yet ive not decieded upon.
Nice to have
• Perhaps incorporate shapes, texture and colours that convey a feel of the attached photo of a blue bird of paradise. The blue fine overlapping and interlocking feather patterns are appealing perhaps as a background and the other colours used in boarders ? Abstract is fine as would be symbolic images or tribal ambience. The company is all about blending humanity in all its forms with the environment.

```html
<!DOCTYPE html>
<html lang="en">
<head>
<meta charset="utf-8">
<title>Reefline Ecology — Home</title>
<link rel="stylesheet" href="https://fonts.googleapis.com/css2?family=Source+Sans+3:wght@400;600;700&display=swap">
<style>
  :root {
    --page-bg: #ffffff;
    --bar-top: #45d0ea;
    --bar-bottom: #1896b3;
    --bar-divider: rgba(255,255,255,0.45);
    --bar-divider-dark: rgba(0,80,100,0.35);
    --text-dark: #222222;
    --text-body: #3a3a3a;
    --link: #17809c;
    --frame: #e2e2e2;
    --white: #ffffff;
    --dot-active: #7fb9c9;
    --dot-idle: #8a8a8a;
  }
  * { margin: 0; padding: 0; box-sizing: border-box; }
  html, body { width: 1200px; height: 1031px; overflow: hidden; background: var(--page-bg); }
  body { position: relative; font-family: "Source Sans 3", "Myriad Pro", sans-serif; color: var(--text-body); }
  a { color: var(--link); text-decoration: none; }

  .nav-bar {
    position: absolute; left: 141px; top: 42px; width: 918px; height: 31px;
    border-radius: 14px;
    background: linear-gradient(var(--bar-top), var(--bar-bottom));
  }
  .nav-list { position: absolute; right: 0; top: 0; height: 31px; display: flex; list-style: none; }
  .nav-list li {
    height: 31px; line-height: 31px; color: var(--white); font-size: 14px; text-align: center;
    border-left: 1px solid var(--bar-divider-dark); box-shadow: inset 1px 0 0 var(--bar-divider);
  }
  .nav-list li:nth-child(1) { width: 79px; }
  .nav-list li:nth-child(2) { width: 98px; }
  .nav-list li:nth-child(3) { width: 125px; }
  .nav-list li:nth-child(4) { width: 94px; }
  .nav-list li:nth-child(5) { width: 123px; }

  .brand {
    position: absolute; left: 155px; top: 0; width: 120px; height: 118px;
    border-radius: 50%; background: var(--white);
    display: flex; align-items: center; justify-content: center; text-align: center;
    font-size: 15px; font-weight: 600; line-height: 17px; color: var(--bar-bottom);
  }

  .photo { position: absolute; }
  .hero-photo { left: 141px; top: 87px; width: 614px; height: 282px;
    background: radial-gradient(ellipse at 45% 60%, #5f8f3a, #3f8a28 45%, #7cc04a 100%); }

  .hero-title { position: absolute; left: 786px; top: 102px; font-size: 28px; font-weight: 700;
    line-height: 34px; color: var(--text-dark); letter-spacing: 0.5px; }
  .hero-text { position: absolute; left: 789px; top: 211px; width: 245px; font-size: 12.5px; line-height: 17.8px; letter-spacing: 0.3px; }
  .hero-dots { position: absolute; left: 886px; top: 351px; display: flex; gap: 5px; }
  .hero-dots span { width: 9px; height: 9px; border-radius: 50%; background: var(--dot-active); }
  .hero-dots span:last-child { background: var(--dot-idle); }

  .section-title { position: absolute; font-size: 26px; font-weight: 400; color: var(--text-dark); letter-spacing: 0.5px; }
  .body-text { position: absolute; font-size: 12.5px; letter-spacing: 0.3px; }
  .more-link { position: absolute; font-size: 12.5px; letter-spacing: 0.3px; }

  .welcome-text { left: 141px; top: 424px; width: 512px; line-height: 19.6px; }
  .news-date { position: absolute; left: 719px; top: 427px; font-size: 14px; font-weight: 700; color: var(--text-dark); letter-spacing: 0.5px; }
  .news-text { left: 718px; top: 450px; width: 345px; line-height: 16px; }

  .thumb { position: absolute; width: 137px; height: 132px; background: var(--white);
    border: 1px solid var(--frame); box-shadow: 0 0 3px rgba(0,0,0,0.15); padding: 3px; }
  .thumb .photo { position: static; width: 100%; height: 100%; }
  .story-frame { width: 369px; }

  .story-lead { left: 698px; top: 783px; width: 345px; font-size: 13.5px; line-height: 19.6px; }
  .story-text { left: 698px; top: 864px; width: 345px; font-size: 11.5px; line-height: 19.5px; }

  .site-footer {
    position: absolute; left: 141px; top: 963px; width: 918px; height: 68px;
    background: linear-gradient(var(--bar-top), var(--bar-bottom));
    color: var(--white); text-align: center; font-size: 10.5px; letter-spacing: 0.3px; line-height: 16px; padding-top: 21px;
  }
</style>
</head>
<body>
  <header>
    <nav class="nav-bar">
      <ul class="nav-list">
        <li>Home</li><li>About us</li><li>Our Activities</li><li>Services</li><li>Contact us</li>
      </ul>
    </nav>
    <div class="brand">Reefline<br>Ecology</div>
  </header>

  <section class="hero">
    <div class="photo hero-photo" role="img" aria-label="Close-up of a banded-wing fly on a green leaf"></div>
    <h1 class="hero-title">Encompassing<br>Culture, Custom<br>&amp; Science</h1>
    <p class="hero-text">Lorem Ipsum is simply dummy text of the printing and typesetting industry. Lorem Ipsum has been the industry's standard dummy text ever since the 1500s, when an unknown printer took a galley of type and scrambled it to make a type specimen book.</p>
    <div class="hero-dots"><span></span><span></span><span></span></div>
  </section>

  <section class="welcome">
    <h2 class="section-title" style="left:141px; top:384px;">Welcome</h2>
    <p class="body-text welcome-text">Lorem Ipsum is simply dummy text of the printing and typesetting industry. Lorem Ipsum has been the industry's standard dummy text ever since the 1500s, when an unknown printer took a galley of type and scrambled it to make a type specimen book. Ipsum has been the industry's standard dummy text ever since the 1500s, when an unknown printer took a galley of type and scrambled it to make a type specimen book. Ipsum has been the industry's</p>
    <a class="more-link" href="#" style="left:605px; top:545px;">view all</a>
  </section>

  <section class="news">
    <h2 class="section-title" style="left:718px; top:386px;">Latest News</h2>
    <p class="news-date">05 - 12 - 12</p>
    <p class="body-text news-text">Lorem Ipsum is simply dummy text of the printing and type-setting industry. Lorem Ipsum has been the industry's standard dummy text ever since the 1500s, when an unknown printer took a galley of type and scrambled it to make a type specimen book.</p>
    <a class="more-link" href="#" style="left:719px; top:545px;">view all news</a>
  </section>

  <section class="projects">
    <h2 class="section-title" style="left:141px; top:582px;">Our Projects</h2>
    <div class="thumb" style="left:156px; top:627px;"><div class="photo" role="img" aria-label="Young crops in tilled soil" style="background:linear-gradient(#6a7a3a,#5a4634);"></div></div>
    <div class="thumb" style="left:325px; top:627px;"><div class="photo" role="img" aria-label="Water sampling funnel in a garden" style="background:linear-gradient(#4f6a32,#3a3a30);"></div></div>
    <div class="thumb" style="left:494px; top:627px;"><div class="photo" role="img" aria-label="People working in a hillside field" style="background:linear-gradient(#5e7d3e,#7a5e48);"></div></div>
    <div class="thumb" style="left:156px; top:801px;"><div class="photo" role="img" aria-label="Green fruit dove held in hands" style="background:linear-gradient(135deg,#4a6a5a,#3d8a3a 55%,#a08a6a);"></div></div>
    <div class="thumb" style="left:325px; top:801px;"><div class="photo" role="img" aria-label="Furry brown marsupial" style="background:radial-gradient(circle at 50% 55%,#5a4a30,#7a9a60);"></div></div>
    <div class="thumb" style="left:494px; top:801px;"><div class="photo" role="img" aria-label="Bat wing at night" style="background:linear-gradient(135deg,#0a0a0a 30%,#8a6a40 60%,#0a0a0a);"></div></div>
  </section>

  <section class="story">
    <h2 class="section-title" style="left:685px; top:582px;">Our Story</h2>
    <div class="thumb story-frame" style="left:689px; top:627px;"><div class="photo" role="img" aria-label="Cuscus resting on a branch among leaves" style="background:linear-gradient(90deg,#5a7a2a,#6a5a3a 45%,#7a9a40);"></div></div>
    <p class="body-text story-lead">Lorem Ipsum is simply dummy text of the printing and typesetting industry. Lorem Ipsum has been the indus-try's standard dummy text ever since the 1500s,</p>
    <p class="body-text story-text">when an unknown printer took a galley of type and scrambled it to make a type specimen book.</p>
    <a class="more-link" href="#" style="left:1013px; top:919px;">view all</a>
  </section>

  <footer class="site-footer">
    <p>© 2012 Reefline Ecology</p>
    <p>Terms of Service - Privacy Policy - Program Policies</p>
  </footer>
</body>
</html>
```